IT Company needs Website for new Web and Mobile products for Sports and Fitness

Background:

We developed web based white label frontend web solution, backend services and white label mobile apps for to log, analyze, share and control sport and fitness activities. The name of this product suite is "Trevantix" (http://trevantix-example.com)

This products will be used by customers that provide platforms and community systems for sport and fitness. One of the major USP's is, that our technology i open for nearly all common formats, devices and apps out in the market. This means, you can just upload your data directly from device, file or app - e.G. Kestrel, Bolvane, Ravelo, StrideVault, Pacelumo, Zembra and much others.

Two current concrete examples/References

(1) MyQuorel
It's an international platform from quorel for runners. It provides individual training lans and a training log. MyQuorel uses the Backend Product "Trevantix Hub" (see http://hub.trevantix-example.net for a landing page) to integrate device, file and app support. Before this, every user has to track his training with manual inputs

(2) Paceharbor and fen-zine
Both are German customers. Paceharor is focused on runners. fen-zine is focused on Triatheletes. Both use the Product "Trevantix Web". This is a complete web solution with web based frontend solutions for athletes and coaches.

What do we need?
We need website layout for B2B for our products. We don't need lot's of pages. We need the pretty and nice layout, so we can derive the pages we need.

IMPORTANT
We don't talk about the webpages for the product itself (this will be a different project in future). We talk about a website, explaining the products)
Updates

Hi all,

we just start reviewing the first designs, and try to give feedback as detailed as possible. We attached a PDF document, to describe the the products a little bit more detailed. 

As written in the description, in the end we have two different sections. One is the usual stuff like "start page", "about", "contact", "disclaimer", "pricing", "blah...." and one will be the Developer Section, the "Tec Section". This ist aimed to developers (of our customers) that will integrate our products in there existing system or which will integrate our services in there own software.  This "pages" are more like "documentation", so easy to read and cool to look at (cause developers likes it cool, but straight)

Dear all,

we just do the final review. Cause this week is with heavy load, it takes some time...

Cheers

Odell

Target Market(s)

* Platforms and Communities for sport, health and fitness
* Gyms

Industry/Entity Type

Concrete

Font styles to use
Sans Serif

Requirements
Must have
• * Templates shall base on bootstrap. If not, it shall be easily realized on our site with bootstrap or out of the box "full responsive"

* HTML5 / CSS3
Nice to have
• PAGES
- Start Page
- Generic Template (from which we can derive additional pages)
- Contact Page
- Disclaimer Page
- Blog/News Page
- "About us" Page (can be combined with disclaimer)
- One Example product page (in end we have 3 products), shall show (if you need product details, let me know)
- product and it's description
- pricing information
- Add-Ons for the product
- Developer Section Page (Start Point for developers, where the finde "basic technical concepts and developer API's
- Example Developer Page for technical concept
- Example Developer Page for API

LOGO ISSUE
You can use an align to the Logo attached OR provide a new logo. The given logo is a logo for our own B2C Website http://trevantix-example.net. It's not really necessary, that the logo or the color must be used for the product website. Maybe it will be better if it's a complete new one, to avoid irritation between Trevantix as a B2B product and trevantix-example.net as a B2C platform.
Should not have
• No Flash and other proprietary technologies

```html
<!DOCTYPE html>
<html lang="en">
<head>
<meta charset="utf-8">
<title>Trevantix – Contact</title>
<link href="https://fonts.googleapis.com/css2?family=PT+Sans:ital,wght@0,400;0,700;1,400&family=PT+Sans+Narrow:wght@400;700&display=swap" rel="stylesheet">
<style>
:root{
  --orange:#e8790f;
  --orange-dark:#d96a00;
  --gold:#e9a20b;
  --ink:#3c3c3c;
  --navy:#1f3247;
  --muted:#8a8a8a;
  --line:#dcdcdc;
  --panel:#f5f5f5;
  --footer:#1c1c1c;
}
*{box-sizing:border-box;margin:0;padding:0}
html,body{width:1200px;height:1034px;overflow:hidden;background:#fff;font-family:"PT Sans",Arial,sans-serif;color:var(--ink)}
.page{position:relative;width:1200px;height:1034px}

.site-header{position:absolute;left:0;top:0;width:1200px;height:91px;background:#fff}
.brand{position:absolute;left:182px;top:22px;display:flex;align-items:center;gap:8px}
.brand-mark{width:14px;height:14px;background:var(--orange)}
.brand-name{font-size:32px;font-weight:700;color:var(--orange);line-height:1}
.main-nav{position:absolute;top:34px;left:406px;display:flex}
.main-nav a{display:block;height:24px;line-height:24px;padding:0 26px;font-size:11px;color:#555;text-decoration:none;border-left:1px solid var(--line);text-transform:uppercase}
.main-nav a:first-child{border-left:none}

.hero{position:absolute;left:0;top:91px;width:1200px;height:424px;overflow:hidden}
.hero-photo{position:absolute;inset:0;
  background:
   radial-gradient(ellipse 260px 200px at 900px 340px,#c9302a 0%,rgba(201,48,42,0) 70%),
   radial-gradient(ellipse 420px 260px at 300px 120px,#fde4a8 0%,rgba(253,228,168,0) 75%),
   linear-gradient(180deg,#f1c27a 0%,#e8a560 45%,#c7744a 80%,#a45a3e 100%)}
.hero-title{position:absolute;left:182px;top:116px;font-family:"PT Sans Narrow",Arial,sans-serif;font-weight:700;font-size:35px;line-height:41px;text-transform:uppercase}
.hero-title .accent{color:var(--orange);display:block}
.hero-title .main{color:var(--ink);display:block}
.signup{position:absolute;left:180px;top:216px;width:382px;height:39px;background:#fff;border:1px solid #d7d7d7;border-radius:3px}
.signup-label{position:absolute;left:16px;top:13px;font-size:10px;color:#888;text-transform:uppercase}
.signup-btn{position:absolute;right:1px;top:1px;width:132px;height:35px;border-radius:3px;background:linear-gradient(#f4b626,#d98d06);color:#fff;font-size:15px;text-align:center;line-height:35px;text-transform:uppercase;font-family:"PT Sans Narrow",Arial,sans-serif}
.hero-arrow{position:absolute;top:179px;width:42px;height:42px}
.hero-arrow.prev{left:87px}
.hero-arrow.next{left:1081px}
.hero-dot{position:absolute;left:979px;top:403px;width:10px;height:10px;border-radius:50%;background:#e6e6e6}

.section-title{position:absolute;left:213px;top:544px;font-family:"PT Sans Narrow",Arial,sans-serif;font-weight:700;font-size:24px;color:var(--navy)}
.section-title span{color:var(--orange)}
.section-rule{position:absolute;left:213px;top:590px;width:413px;height:4px;background:radial-gradient(ellipse at center,rgba(0,0,0,.08),rgba(0,0,0,0) 70%)}

.query{position:absolute;left:207px;top:643px;width:223px;height:260px;border-radius:8px;background:linear-gradient(#6b6b6b,#3a3a3a);border:1px solid #2e2e2e;box-shadow:0 2px 3px rgba(0,0,0,.25)}
.query-head{height:43px;border-bottom:1px solid #505050;position:relative}
.query-head svg{position:absolute;left:8px;top:7px}
.query-title{position:absolute;left:61px;top:12px;color:#fff;font-size:18px;font-variant:small-caps;font-weight:700;letter-spacing:.5px}
.field{position:absolute;left:16px;width:190px;height:26px;background:#fff;border:1px solid #c9c9c9;border-radius:2px;font-size:10px;font-style:italic;color:#888;padding:7px 14px}
.field.name{top:55px}.field.email{top:91px}.field.phone{top:126px}
.field.message{top:161px;height:45px;padding-top:16px}
.submit{position:absolute;left:128px;top:218px;width:77px;height:27px;border-radius:3px;background:linear-gradient(#4a4a4a,#111);color:#fff;font-style:italic;font-size:14px;text-align:center;line-height:27px;text-transform:uppercase;font-family:"PT Sans Narrow",Arial,sans-serif}

.contact-card{position:absolute;left:465px;top:643px;width:515px;height:259px;background:var(--panel);border:1px solid var(--line);border-radius:8px}
.map{position:absolute;left:41px;top:23px;width:217px;height:215px;border:1px solid #cfcfcf;background:linear-gradient(135deg,#ece9e3,#e3dfd8)}
.contact-info{position:absolute;left:307px;top:38px;font-size:11px;color:var(--ink)}
.contact-info h3{font-weight:400;font-size:17px;margin-bottom:22px}
.contact-info p{line-height:20.5px;margin-bottom:20px}

.footer-dots{position:absolute;left:0;top:952px;width:1200px;border-top:1px dotted #999}
.site-footer{position:absolute;left:0;top:956px;width:1200px;height:78px;background:linear-gradient(#2a2a2a,var(--footer))}
.social{position:absolute;left:209px;top:19px;display:flex;gap:11px}
.social span{display:block;width:22px;height:22px;border-radius:2px}
.copyright{position:absolute;right:229px;top:17px;font-size:11px;color:#ccc}
</style>
</head>
<body>
<div class="page">
  <header class="site-header">
    <div class="brand"><span class="brand-mark"></span><span class="brand-name">Trevantix</span></div>
    <nav class="main-nav">
      <a href="#">Home</a><a href="#">Trevantix</a><a href="#">Fitness Cloud</a><a href="#">References</a><a href="#">Products</a><a href="#">Services</a>
    </nav>
  </header>

  <section class="hero">
    <div class="hero-photo" role="img" aria-label="Runner's feet in red running shoes on a road in warm sunrise light"></div>
    <h1 class="hero-title"><span class="accent">Die offene Sport- und</span><span class="main">Fitnessplatform fur jeden Sport</span></h1>
    <div class="signup"><span class="signup-label">What's your email address :</span><span class="signup-btn">Join for free</span></div>
    <svg class="hero-arrow prev" viewBox="0 0 42 42"><circle cx="21" cy="21" r="20" fill="rgba(255,255,255,.15)" stroke="rgba(255,255,255,.7)" stroke-width="2"/><path d="M25 11 L13 21 L25 31 Z" fill="rgba(255,255,255,.7)"/></svg>
    <svg class="hero-arrow next" viewBox="0 0 42 42"><circle cx="21" cy="21" r="20" fill="rgba(255,255,255,.15)" stroke="rgba(255,255,255,.7)" stroke-width="2"/><path d="M17 11 L29 21 L17 31 Z" fill="rgba(255,255,255,.7)"/></svg>
    <span class="hero-dot"></span>
  </section>

  <h2 class="section-title">Contact <span>Us</span></h2>
  <div class="section-rule"></div>

  <form class="query">
    <div class="query-head">
      <svg width="38" height="30" viewBox="0 0 38 30"><g transform="rotate(-14 19 15)"><rect x="3" y="5" width="32" height="21" rx="2" fill="#f2f2f2"/><path d="M3 6 L19 18 L35 6" fill="none" stroke="#bbb" stroke-width="1.5"/></g></svg>
      <span class="query-title">Query</span>
    </div>
    <div class="field name">Name</div>
    <div class="field email">Email</div>
    <div class="field phone">Phone</div>
    <div class="field message">Message</div>
    <div class="submit">Submit</div>
  </form>

  <section class="contact-card">
    <div class="map" role="img" aria-label="Street map showing the office location with a red pin"></div>
    <div class="contact-info">
      <h3>Contact Us</h3>
      <p>#17 Harlowe Road, Fenwick Park,<br>Southgate district office.</p>
      <p>Phone: +91 804417265<br>Tollfree: (006) 60917354</p>
      <p>E-mail: info@trevantix-example.com</p>
    </div>
  </section>

  <div class="footer-dots"></div>
  <footer class="site-footer">
    <div class="social">
      <span style="background:#3b5998"></span>
      <span style="background:#39b6e6"></span>
      <span style="background:#444"></span>
      <span style="background:#f0a21c"></span>
      <span style="background:#c4211d"></span>
      <span style="background:#7f9bb0"></span>
    </div>
    <p class="copyright">© 2013 trevantix-example.com, All rights reserved</p>
  </footer>
</div>
</body>
</html>
```